Investment firm needs website redesign

we want to change our site with a trendy new design. We are an investment trading firm dealing in currencies etc for retail clients. We are looking for new ideas for our website design which shows class and international reach. We want the inner pages also to be designed especially the look. We do not want the typical designs used by most sites and are looking for something new and interesting. you can review our current site www.trovanique-exchange.com.

Target Market(s)

international

Industry/Entity Type

Forex

Coding

Coded - Design and coding required

Number of Pages Required

5+ page

Font styles to use
Sans Serif

Colors

Designer to choose colors to be used in the design.

Requirements
Must have
• responsive, easy to load
Nice to have
• something trendy yet sophisticated. technology is an important part of our business
Should not have
• do not want the typical designs used by most websites

```html
<!DOCTYPE html>
<html lang="en">
<head>
<meta charset="utf-8">
<title>Trovanique Exchange</title>
<link href="https://fonts.googleapis.com/css2?family=Lato:wght@400;700;900&display=swap" rel="stylesheet">
<style>
:root{
  --gold:#f2b632;
  --navy:#1a2a3b;
  --navy-deep:#13202e;
  --ink:#1d1d1d;
  --muted:#5a5a5a;
  --line:#cfcfcf;
  --green:#5cd65c;
  --sand:#efe4c6;
  --foot:#f1f1f1;
  --white:#ffffff;
}
*{box-sizing:border-box;margin:0;padding:0}
html,body{width:1200px;height:2590px;overflow:hidden}
body{font-family:'Lato',sans-serif;color:var(--ink);background:var(--white);position:relative}
.abs{position:absolute}

/* header */
.site-header{position:absolute;left:0;top:0;width:1200px;height:104px;background:var(--white)}
.brand{position:absolute;left:98px;top:24px;display:flex;align-items:center;gap:12px}
.brand-mark{width:48px;height:48px;border-radius:50%;background:var(--navy)}
.brand-name{font-weight:900;font-size:25px;color:var(--navy);line-height:1}
.brand-name small{display:block;font-size:12px;font-weight:900;letter-spacing:2px;margin-top:4px}
.top-links{position:absolute;right:100px;top:18px;font-size:15px;color:#222;display:flex;gap:12px;align-items:center}
.top-links .ico{color:var(--gold)}
.main-nav{position:absolute;right:100px;top:62px;display:flex;gap:19px;font-size:15px;font-weight:700;color:#222}
.main-nav .active{color:var(--gold);font-weight:400}

/* hero */
.hero{position:absolute;left:0;top:104px;width:1200px;height:530px;
  background:radial-gradient(circle at 380px 150px,#6a5a3a 0,#3a3428 25%,transparent 45%),linear-gradient(110deg,#3b3a36 0%,#2a2d33 45%,#13203a 75%,#0d1a33 100%)}
.hero-title{position:absolute;left:0;width:1200px;top:110px;text-align:center;color:var(--white);font-size:59px;font-weight:900}
.hero-lead{position:absolute;left:240px;width:720px;top:198px;text-align:center;color:var(--white);font-size:20px;line-height:1.65}
.search{position:absolute;left:243px;top:307px;width:714px;height:59px;background:var(--white);display:flex}
.search .ticker{width:120px;border-right:1px solid var(--line);display:flex;align-items:center;justify-content:space-between;padding:0 16px;font-size:16px;color:#333}
.search .field{flex:1;display:flex;align-items:center;padding-left:30px;font-size:16px;color:#888}
.search .go{width:66px;background:var(--gold);display:flex;align-items:center;justify-content:center}
.dots{position:absolute;left:563px;top:448px;display:flex;gap:6px}
.dots span{width:13px;height:13px;border-radius:50%;border:2px solid var(--white)}
.dots span:first-child{background:var(--white)}
.live-chat{position:absolute;right:0;top:183px;width:48px;height:155px;background:var(--navy-deep);color:var(--white);font-size:14px;font-weight:700;writing-mode:vertical-rl;transform:rotate(180deg);display:flex;align-items:center;justify-content:center;letter-spacing:1px}

/* live market */
.market{position:absolute;left:0;top:634px;width:1200px;height:112px;background:var(--navy-deep)}
.market-label{position:absolute;left:0;top:0;width:268px;height:112px;background:var(--gold);color:var(--white);font-size:22px;font-weight:700;text-align:center;padding-top:62px}
.market-label::after{content:"";position:absolute;right:-22px;top:34px;border-left:22px solid var(--gold);border-top:22px solid transparent;border-bottom:22px solid transparent}
.market-label svg{position:absolute;left:117px;top:24px}
.quote{position:absolute;top:14px;color:var(--white)}
.quote b{display:block;font-size:20px;font-weight:700;margin-bottom:12px}
.quote span{font-size:14px;display:block;line-height:1.45}
.quote em{font-style:normal;color:var(--green)}
.qsep{position:absolute;top:0;width:1px;height:112px;background:#2d3d50}

/* tabs */
.tabs{position:absolute;top:805px;left:0;width:1200px;display:flex;justify-content:center;gap:30px}
.tabs span{border:1px solid #555;padding:7px 11px;font-size:14px;font-weight:700;color:#222}

/* welcome */
.welcome-title{position:absolute;left:0;width:1200px;top:905px;text-align:center;font-size:33px;font-weight:900;color:var(--navy-deep)}
.welcome-intro{position:absolute;left:200px;width:800px;top:970px;text-align:center;font-size:15px;line-height:2;color:var(--muted)}
.card{position:absolute;top:1088px;width:315px;height:252px;border:1px solid var(--line);text-align:center}
.card-icon{height:62px;margin-top:30px;display:flex;align-items:flex-end;justify-content:center}
.card-title{font-size:20px;font-weight:700;color:#222;margin-top:24px}
.card-text{font-size:14px;line-height:1.85;color:var(--muted);margin-top:14px}
.card-btn{position:absolute;left:50%;bottom:-20px;transform:translateX(-50%);background:var(--gold);color:var(--white);font-size:14px;font-weight:700;border-radius:22px;padding:11px 18px;white-space:nowrap}

/* demo */
.demo{position:absolute;left:0;top:1465px;width:1200px;height:316px;background:linear-gradient(100deg,#2b3442 0%,#3a3f49 40%,#4a4d55 70%,#2e3847 100%)}
.demo-title{position:absolute;left:97px;top:52px;color:var(--white);font-size:32px;font-weight:900}
.demo-list{position:absolute;left:97px;top:112px;list-style:none;color:var(--white);font-size:18px;line-height:2}
.demo-try{position:absolute;left:97px;top:200px;border:2px solid var(--white);border-radius:30px;color:var(--white);font-weight:700;font-size:15px;padding:15px 26px}
.devices{position:absolute;left:690px;top:29px;width:415px;height:233px;border-radius:6px;background:linear-gradient(135deg,#1c1c1c,#3f4a58 60%,#22262c)}

/* update */
.update{position:absolute;left:0;top:1781px;width:1200px;height:74px;background:var(--sand);overflow:hidden}
.update-label{position:absolute;left:0;top:0;width:219px;height:74px;background:var(--gold);color:var(--white);font-size:20px;font-weight:700;padding:26px 0 0 66px}
.update-text{position:absolute;left:254px;top:24px;font-size:18px;font-weight:700;color:#222;white-space:nowrap}

/* partners */
.partners-title{position:absolute;left:0;width:1200px;top:1942px;text-align:center;font-size:33px;font-weight:900;color:var(--navy-deep)}
.pbox{position:absolute;top:2024px;height:90px;border:1px solid var(--line);display:flex;align-items:center;justify-content:center}
.pbox i{display:block}
.parrow{position:absolute;top:2049px;width:40px;height:40px;border:1px solid #666;border-radius:50%;display:flex;align-items:center;justify-content:center}

/* footer */
.site-footer{position:absolute;left:0;top:2216px;width:1200px;height:374px;background:var(--foot)}
.site-footer .brand{left:107px;top:105px}
.fcol{position:absolute;top:62px}
.fcol h4{font-size:17px;font-weight:700;color:#222;margin-bottom:14px}
.fcol li{list-style:none;font-size:14px;color:var(--muted);line-height:27.5px}
.fdivider{position:absolute;left:98px;top:278px;width:1002px;height:1px;background:var(--line)}
.copy{position:absolute;left:98px;top:316px;font-size:13px;color:#333}
.social{position:absolute;left:964px;top:310px;display:flex;gap:6px}
.social span{width:30px;height:30px;border:1px solid #333;border-radius:50%}
</style>
</head>
<body>

<header class="site-header">
  <div class="brand"><span class="brand-mark"></span><span class="brand-name">TROVANIQUE<small>EXCHANGE</small></span></div>
  <div class="top-links"><span><span class="ico">&#9679;</span> Open Account</span><span>|</span><span><span class="ico">&#9993;</span> Contact</span><span>|</span><span>Eng &#9662;</span></div>
  <nav class="main-nav"><span class="active">Home</span><span>About</span><span>Products &amp; Services</span><span>Trading Platforms</span><span>Trading Info</span><span>Partner Programe</span><span>Research</span>
    <svg width="16" height="16" viewBox="0 0 16 16"><circle cx="6.5" cy="6.5" r="5" fill="none" stroke="#222" stroke-width="2"/><line x1="10" y1="10" x2="15" y2="15" stroke="#222" stroke-width="2.4"/></svg></nav>
</header>

<section class="hero" role="img" aria-label="Laptop on a desk with a digital currency coin and a glowing network globe">
  <h1 class="hero-title">TROVANIQUE EXCHANGE</h1>
  <p class="hero-lead">Trovanique offers the White Label Program to Individuals &amp;Institutions that want to establish a brand name in the global markets.</p>
  <div class="search">
    <div class="ticker">Ticker <span>&#8964;</span></div>
    <div class="field">Search</div>
    <div class="go"><svg width="22" height="22" viewBox="0 0 16 16"><circle cx="6.5" cy="6.5" r="5" fill="none" stroke="#fff" stroke-width="2"/><line x1="10" y1="10" x2="15" y2="15" stroke="#fff" stroke-width="2.4"/></svg></div>
  </div>
  <div class="dots"><span></span><span></span><span></span><span></span></div>
  <div class="live-chat">&#9675; LIVE CHAT</div>
</section>

<section class="market">
  <div class="market-label">
    <svg width="34" height="26" viewBox="0 0 34 26"><g fill="#fff"><rect x="2" y="14" width="4" height="10"/><rect x="9" y="6" width="4" height="18"/><rect x="16" y="10" width="4" height="14"/><rect x="23" y="2" width="4" height="22"/><rect x="0" y="24" width="32" height="2"/></g></svg>
    LIVE MARKET
  </div>
  <div class="quote" style="left:314px"><b>BNB/BTC</b><span><em>0.0014713</em> $11.64</span><span>Volume: 4,645.73 BTC</span></div>
  <div class="qsep" style="left:494px"></div>
  <div class="quote" style="left:530px"><b>ETH/BTC</b><span><em>0.0014713</em> $11.64</span><span>Volume: 4,645.73 BTC</span></div>
  <div class="qsep" style="left:710px"></div>
  <div class="quote" style="left:746px"><b>TRX/BTC</b><span><em>0.0014713</em> $11.64</span><span>Volume: 4,645.73 BTC</span></div>
  <div class="qsep" style="left:926px"></div>
  <div class="quote" style="left:962px"><b>LTC/USD</b><span><em>0.0014713</em> $11.64</span><span>Volume: 4,645.73 BTC</span></div>
  <svg class="abs" style="left:1143px;top:44px" width="14" height="24" viewBox="0 0 14 24"><polyline points="2,2 12,12 2,22" fill="none" stroke="#fff" stroke-width="2"/></svg>
</section>

<div class="tabs"><span>CFDS</span><span>SPOT</span><span>FUTURES</span><span>OPTIONS</span><span>BONDS</span><span>STOCKS</span><span>WEB LOGIN</span><span>MOBILE TRADING</span></div>

<section class="welcome">
  <h2 class="welcome-title">WELCOME TO TROVANIQUE</h2>
  <p class="welcome-intro">Trovanique offers the White Label Program to Individuals &amp;Institutions that want to establish a brand name in the global markets. As a White Label partner, you will be provided with a Platform with your Brand or Logo.</p>

  <div class="card" style="left:98px">
    <div class="card-icon"><svg width="52" height="56" viewBox="0 0 52 56"><circle cx="26" cy="15" r="13" fill="#13202e"/><path d="M2 56 Q2 31 26 31 Q50 31 50 56Z" fill="#13202e"/></svg></div>
    <h3 class="card-title">MULTI-ACCOUNT MANAGER</h3>
    <p class="card-text">Vanta Pro and Trader are 2 online<br>platforms provided</p>
    <span class="card-btn">READ MORE</span>
  </div>
  <div class="card" style="left:442px">
    <div class="card-icon"><svg width="62" height="56" viewBox="0 0 62 56"><rect x="3" y="8" width="44" height="44" rx="4" fill="none" stroke="#13202e" stroke-width="5"/><path d="M24 38 L27 28 L52 3 L60 11 L35 36Z" fill="#13202e"/></svg></div>
    <h3 class="card-title">CONTRACT SPECIFICATIONS</h3>
    <p class="card-text">The Trovanique EBroker offers money<br>managers and traders</p>
    <span class="card-btn">READ MORE</span>
  </div>
  <div class="card" style="left:786px">
    <div class="card-icon"><svg width="66" height="60" viewBox="0 0 66 60"><g fill="#13202e"><circle cx="24" cy="36" r="16"/><circle cx="50" cy="16" r="11"/></g><circle cx="50" cy="16" r="4" fill="#fff"/><g stroke="#13202e" stroke-width="7"><line x1="24" y1="15" x2="24" y2="57"/><line x1="3" y1="36" x2="45" y2="36"/><line x1="9" y1="21" x2="39" y2="51"/><line x1="39" y1="21" x2="9" y2="51"/></g><circle cx="24" cy="36" r="6" fill="#fff"/></svg></div>
    <h3 class="card-title">HOW TO OPEN AN ACCOUNT</h3>
    <p class="card-text">Welcome to the Trovanique experience,<br>Our account...</p>
    <span class="card-btn">READ MORE</span>
  </div>
</section>

<section class="demo" role="img" aria-label="Blurred laptop keyboard background">
  <h2 class="demo-title">CREATE A DEMO ACCOUNT NOW</h2>
  <ul class="demo-list"><li>*&nbsp; Get started in just a few seconds</li><li>*&nbsp; For free and under real conditions</li></ul>
  <span class="demo-try">TRY IT FOR FREE</span>
  <div class="devices" role="img" aria-label="Monitor, tablet and phone showing trading charts"></div>
</section>

<section class="update">
  <div class="update-label">UPDATE</div>
  <div class="update-text">Forex - Pound Hits Day's Highs after UK Services Data &nbsp;&nbsp;|&nbsp;&nbsp; Forex - Euro Steady, Dollar Firm as Markets Await Fresh Cues</div>
</section>

<section class="partners">
  <h2 class="partners-title">PARTNERS</h2>
  <div class="parrow" style="left:28px"><svg width="10" height="16" viewBox="0 0 10 16"><polyline points="8,2 2,8 8,14" fill="none" stroke="#444" stroke-width="2"/></svg></div>
  <div class="pbox" style="left:98px;width:187px"><i style="width:60px;height:60px;border-radius:50%;background:#2b3f8a"></i></div>
  <div class="pbox" style="left:302px;width:187px"><i style="width:110px;height:38px;border-radius:4px;background:#fff;border:1px solid #888"></i></div>
  <div class="pbox" style="left:508px;width:185px"><i style="width:144px;height:46px;border-radius:6px;background:#111"></i></div>
  <div class="pbox" style="left:712px;width:186px"><i style="width:50px;height:56px;border-radius:50%;background:#2a5aa8"></i></div>
  <div class="pbox" style="left:915px;width:185px"><i style="width:138px;height:40px;border-radius:3px;background:#dbe3d0"></i></div>
  <div class="parrow" style="left:1129px"><svg width="10" height="16" viewBox="0 0 10 16"><polyline points="2,2 8,8 2,14" fill="none" stroke="#444" stroke-width="2"/></svg></div>
</section>

<footer class="site-footer">
  <div class="brand"><span class="brand-mark"></span><span class="brand-name">TROVANIQUE<small>EXCHANGE</small></span></div>
  <div class="fcol" style="left:416px"><h4>Products</h4><ul><li>Cfds</li><li>Forex</li><li>Futures</li><li>Stocks</li><li>Bonds</li><li>Options</li></ul></div>
  <div class="fcol" style="left:572px"><h4>Company</h4><ul><li>Our Regulator</li><li>Compliance</li><li>Auditor</li><li>Global Network</li></ul></div>
  <div class="fcol" style="left:760px"><h4>Trading Platforms</h4><ul><li>Vanta Pro</li><li>Vanta Trader</li><li>Demo</li><li>System Manual</li></ul></div>
  <div class="fcol" style="left:965px"><h4>Partner Program</h4><ul><li>Ibs</li><li>White Labels</li></ul>
    <h4 style="margin-top:14px">Open An Account</h4><ul><li>Account Form</li><li>Product Guide</li></ul></div>
  <div class="fdivider"></div>
  <div class="copy">Copyrights &copy; 2018, Trovanique Exchange. All rights reserved.</div>
  <div class="social"><span></span><span></span><span></span><span></span></div>
</footer>

</body>
</html>
```